Marwick Law Letterhead

We need a new letterhead design for a Law Firm. The address for the law firm is 1475 Calloway Street, Suite 210, Houston, Texas 77041. Phone Number: 832-361-9027; Fax Number: 832-614-7359. The logo is uploaded to the project.

```html
<!DOCTYPE html>
<html lang="en">
<head>
<meta charset="utf-8">
<title>Marwick Law Letterhead</title>
<link rel="stylesheet" href="https://fonts.googleapis.com/css2?family=Montserrat:wght@400;500;600&display=swap">
<style>
  :root {
    --backdrop: #e6e6e8;
    --paper: #ffffff;
    --ink: #2b2b2b;
    --navy: #1f3a72;
    --red: #d4151f;
    --red-deep: #8a0712;
  }
  * { box-sizing: border-box; margin: 0; padding: 0; }
  html, body { width: 1200px; height: 960px; overflow: hidden; }
  body {
    background: var(--backdrop);
    font-family: "Montserrat", Arial, sans-serif;
    color: var(--ink);
    position: relative;
  }
  .letterhead {
    position: absolute;
    left: 280px; top: 27px;
    width: 640px; height: 906px;
    background: var(--paper);
    box-shadow: 0 6px 24px rgba(0,0,0,.12);
    overflow: hidden;
  }
  .footer-wave { position: absolute; inset: 0; width: 640px; height: 906px; }
  .brand {
    position: absolute; left: 44px; top: 48px;
    display: flex; align-items: center; gap: 10px;
  }
  .brand-mark { width: 30px; height: 30px; border-radius: 50%; background: var(--navy); }
  .brand-name { font-size: 24px; font-weight: 600; color: var(--navy); letter-spacing: .5px; }
  .recipient {
    position: absolute; left: 92px; top: 150px;
    font-size: 11px; line-height: 15px;
  }
  .letter-body {
    position: absolute; left: 92px; top: 226px; width: 490px;
    font-size: 10.5px; line-height: 14.5px;
  }
  .letter-body p { margin-bottom: 14px; }
  .contact {
    position: absolute; left: 60px; top: 790px;
    color: #fff; font-size: 11px; line-height: 15px;
  }
  .contact-lines { margin-top: 10px; }
  .contact-row { display: flex; align-items: center; gap: 8px; }
  .contact-row svg { width: 11px; height: 11px; fill: #fff; }
</style>
</head>
<body>
  <main class="letterhead">
    <svg class="footer-wave" viewBox="0 0 640 906" aria-hidden="true">
      <defs>
        <linearGradient id="redFill" x1="0" y1="1" x2="1" y2="0">
          <stop offset="0" stop-color="var(--red)"/>
          <stop offset="0.55" stop-color="#b10d18"/>
          <stop offset="1" stop-color="var(--red-deep)"/>
        </linearGradient>
      </defs>
      <path d="M380,684 C490,670 585,648 640,612 L640,630 C590,660 500,680 380,684 Z" fill="url(#redFill)"/>
      <path d="M0,752 C170,702 330,700 460,682 C545,670 605,654 640,636 L640,652 C605,672 545,688 460,700 C330,718 170,724 0,772 Z" fill="var(--navy)"/>
      <path d="M0,778 C170,730 330,724 460,706 C545,694 605,678 640,658 L640,906 L0,906 Z" fill="url(#redFill)"/>
    </svg>

    <header class="brand">
      <span class="brand-mark"></span>
      <span class="brand-name">Marwick Law</span>
    </header>

    <section class="recipient">
      <p>Mr/s</p>
      <p>First Name and Last Name</p>
      <p>Company Name</p>
      <p>Address</p>
    </section>

    <section class="letter-body">
      <p>Lorem ipsum dolor sit amet, consectetur adipiscing sed do eiusmod tempor incididunt laboreet dolore magna aliqua. Ut enim ad minim veniam, quis nostrud exercitation ullamco laboris nisi ut aliquip exea commodo consequat. Lorem ipsum dolor sit amet, consectetur adipiscing sed do eiusmod tempor incididunt labore et dolore magna aliqua. Ut enim</p>
      <p>Lorem ipsum dolor sit amet, consectetur adipiscing sed do eiusmod tempor incididunt labore et dolore magna aliqua. Ut enim ad minim veniam, quis nostrud exercitation ullamco laboris nisi ut aliquip exea commodo consequat. Duis aute irure dolor in reprehenderit in voluptate velit esse cillum irure dolor in reprehenderit in voluptate velit esse irure</p>
      <p>Lorem ipsum dolor sit amet, consectetur adipiscing sed do eiusmod tempor incididunt labore et dolore magna aliqua. Consequat. Duis aute irure dolor in reprehenderit in voluptate velit esse cillum dolore eu fugiat nulla pariatur. Excepteur sint occaecat cupidatat non proident, sunt in culpa qui officia deserunt mollit,</p>
      <p>Lorem ipsum dolor sit amet, consectetur adipiscing sed do eiusmod tempor incididunt labore et dolore magna aliqua. Ut enim Lorem ipsum dolor sit amet, consectetur adipiscing sed do eiusmod tempor incididunt labore et dolore magna aliqua. Ut enim Lorem ipsum aliqua. ipsum</p>
      <p>Lorem ipsum dolor sit amet, consectetur adipiscing sed do eiusmod tempor incididunt labore et dolore magna aliqua. Ut enim ad minim veniam, quis nostrud exercitation ullamco laboris nisi ut aliquip exea commodo consequat. Duis aute irure dolor in reprehenderit in voluptate velit esse irure</p>
    </section>

    <footer class="contact">
      <p>1475 Calloway Street,</p>
      <p>Suite 210, Houston,</p>
      <p>Texas 77041</p>
      <div class="contact-lines">
        <div class="contact-row">
          <svg viewBox="0 0 24 24"><path d="M6.6 10.8a15.1 15.1 0 0 0 6.6 6.6l2.2-2.2c.3-.3.7-.4 1-.2 1.1.4 2.3.6 3.6.6.6 0 1 .4 1 1V20c0 .6-.4 1-1 1A17 17 0 0 1 3 4c0-.6.4-1 1-1h3.5c.6 0 1 .4 1 1 0 1.2.2 2.4.6 3.6.1.3 0 .7-.2 1z"/></svg>
          <span>832-361-9027</span>
        </div>
        <div class="contact-row">
          <svg viewBox="0 0 24 24"><path d="M6 2h10l2 2v5H6zM3 10h18v8h-3v4H6v-4H3zm5 6v4h8v-4z"/></svg>
          <span>832-614-7359</span>
        </div>
      </div>
    </footer>
  </main>
</body>
</html>
```